Social Media Templates for Fieldhouse Raffle Fund

We need a set of Square (1080 x 1080) social media posts.

My company works with sports clubs, helping them to raise money with a lottery.

I need a set of social media image that I can use to appeal to new Fieldhouse Raffle Fund to encourage them to start a lottery with us.

This landing page has worked very well for us https://fieldhouserafflefund.com/fieldhouse-raffle-fund/

THING THAT APPEAL TO CLUBS

No Setup Fees/Start for Free - (We don’t charge any registration fees, or setup fees so you can start raising money from the first draw.)

Start Straight Away - (A club can start raising money straight away.)

Sustainable Income - (The average player plays for 7 years)

Subscription Lottery - (once a player joins, they play until the choose to leave. A club doesn't have to sell tickets every draw to the same people)

All Administration Taken Care Of - (We do all the hard work, so they can focus on running their club.)

Unlimited Income - (There is no limit on the amount of money a club can raise: the more players, the more funds for the club.)

Fundraising reach - (Reach new fans)

50% of the sales is guaranteed profit

£25,000 jackpot - (a person could win £25,000 every week)

Price - (It costs just £1 per week to enter)

Help Your Club - (100% of the profit goes to the club who a player chooses to support)

You can see all the clubs we work with on www.fieldhouserafflefund.com

The images will also be used on Chatterwall. You can see some examples here https://www.chatterwall.com/FieldhouseRaffleFund/ (you may need a proxy to view this page as it is only viewable in the UK, so I have attached some screenshots)

You can find the Fieldhouse Raffle Fund Logo here https://www.logovault.com/winwellgroup/

Target Market(s)

People who are involved with amateur sports in United Kingdom

Industry/Entity Type

Gambling

Font styles to use
Sans Serif

Requirements
Must have
• My project must look great on social social media and encourage people to get in touch about starting a lottery with us.

Adobe Suite files must be provided

```html
<!DOCTYPE html>
<html lang="en">
<head>
<meta charset="utf-8">
<title>Fieldhouse Raffle Fund – Fundraising Reach</title>
<link href="https://fonts.googleapis.com/css2?family=Montserrat:wght@200;400;500;800;900&display=swap" rel="stylesheet">
<style>
  :root {
    --backdrop: #4a4a4a;
    --amber: #f6b63e;
    --amber-deep: #ef9a1f;
    --sky-peach: #f7d6b0;
    --crowd: #5a5d8a;
    --pitch: #6aa746;
    --burnt: #c9570f;
    --shadow-brown: rgba(150, 60, 10, 0.75);
    --white: #ffffff;
    --navy: #27388f;
  }
  * { margin: 0; padding: 0; box-sizing: border-box; }
  html, body {
    width: 1200px; height: 1178px; overflow: hidden;
    background: var(--backdrop);
    font-family: "Montserrat", sans-serif;
  }
  .post {
    position: absolute; left: 125px; top: 114px;
    width: 950px; height: 951px; overflow: hidden;
    background: var(--amber);
  }
  .stadium-photo {
    position: absolute; inset: 0;
    background: linear-gradient(180deg,
      var(--amber) 0%, var(--sky-peach) 30%, #d9c8d0 38%,
      var(--crowd) 48%, #4b4f7e 62%, #5c6a70 70%,
      var(--pitch) 76%, #8a9a3a 82%, var(--amber-deep) 88%, var(--amber) 100%);
  }
  .bottom-band {
    position: absolute; left: 0; right: 0; bottom: 0; height: 128px;
    background: linear-gradient(90deg, var(--amber) 0%, var(--amber-deep) 100%);
  }
  .corner-wedge { position: absolute; inset: 0; }
  .headline {
    position: absolute; left: 0; width: 100%; text-align: center;
    color: var(--white); font-weight: 800; line-height: 1;
    text-shadow: 6px 7px 8px var(--shadow-brown);
  }
  .headline--top { top: 16px; font-size: 112px; letter-spacing: -1px; }
  .headline--top span { display: block; }
  .headline--top span + span { margin-top: 6px; }
  .subline {
    position: absolute; left: 0; width: 100%; top: 362px;
    text-align: center; color: var(--white);
    font-weight: 200; font-size: 78px; letter-spacing: -1px; line-height: 1;
  }
  .divider {
    position: absolute; left: 103px; width: 756px; top: 441px;
    height: 2px; background: var(--white);
  }
  .feature {
    position: absolute; left: 0; width: 100%; top: 442px;
    text-align: center; color: var(--white);
    font-weight: 900; font-size: 126px; letter-spacing: 6px; line-height: 1;
  }
  .ribbons { position: absolute; inset: 0; }
  .cta {
    position: absolute; color: var(--white);
    font-weight: 500; font-size: 44px; line-height: 1; white-space: nowrap;
    left: 142px; top: 716px; transform: rotate(-5deg); transform-origin: left bottom;
  }
  .url {
    position: absolute; color: var(--navy);
    font-weight: 500; font-size: 37px; line-height: 1; white-space: nowrap;
    left: 126px; top: 774px; transform: rotate(-5deg); transform-origin: left bottom;
  }
  .price {
    position: absolute; left: 0; width: 100%; bottom: 20px;
    text-align: center; color: var(--white);
    font-weight: 900; font-size: 108px; line-height: 1; letter-spacing: -1px;
    text-shadow: 6px 7px 6px var(--shadow-brown);
  }
  .price .amount { font-size: 136px; }
  .brand-name {
    position: absolute; left: 756px; top: 700px; width: 164px;
    text-align: center; color: var(--white);
    font-weight: 800; font-size: 27px; line-height: 1.1;
  }
</style>
</head>
<body>
  <main class="post">
    <div class="stadium-photo" role="img" aria-label="Packed football stadium at sunset with crowd in the stands, groundstaff on the pitch and cheering fan silhouettes"></div>

    <svg class="corner-wedge" viewBox="0 0 950 951" aria-hidden="true">
      <polygon points="500,951 950,700 950,951" fill="var(--amber-deep)" opacity="0.85"/>
    </svg>
    <div class="bottom-band"></div>

    <h1 class="headline headline--top"><span>FUNDRAISING</span><span>REACH</span></h1>

    <p class="subline">REACH</p>
    <div class="divider"></div>
    <p class="feature">NEW FANS</p>

    <svg class="ribbons" viewBox="0 0 950 951" aria-hidden="true">
      <polygon points="116,768 138,716 572,685 681,716" fill="var(--burnt)"/>
      <polygon points="72,785 736,729 716,788 107,822" fill="var(--white)"/>
    </svg>
    <p class="cta">JOIN OUR LOTTERY</p>
    <p class="url">www.fieldhouserafflefund.com</p>

    <p class="brand-name">Fieldhouse Raffle Fund</p>

    <p class="price">JUST <span class="amount">£1</span> AWEEK</p>
  </main>
</body>
</html>
```